Custom Cabinet Shop Needs a website design

Hi,
We need a website for a Custom Cabinet Shop and Cabinet parts manufacturing business.
The business has two sides to it. One side provides custom Kitchens, vanities, entertainment units, offices and what not to homeowners and contractors.
The 2nd side of the business provides built to order cabinet boxes and other parts required to put together a project to other cabinet shops, small contractors looking to install there own cabinets.
Website will need a Gallery to display work.
Color scheme to go well with logo.
current website is www.brambleoakcustomcabinets.com
being changed to www.brambleoak.ca
Logo Included in attached files.
Tagline "Joinery with Spirit"
Mission Statement "Our passion is to deliver inspired cabinetry solutions to suit all your needs, supported by our phenomenal star class customer service"
The website should convey quality and professionalism.
Thank you.
Homeowners/ Contractors
Entertainment

```html
<!DOCTYPE html>
<html lang="en">
<head>
<meta charset="utf-8">
<title>Brambleoak Custom Cabinets</title>
<link href="https://fonts.googleapis.com/css2?family=Exo+2:wght@400;500;600&family=Roboto:wght@400;500&display=swap" rel="stylesheet">
<style>
:root{
  --orange:#e0431a;
  --black:#0a0a0a;
  --ink:#1c1c1c;
  --grey-text:#666;
  --panel:#e7e7e7;
  --white:#fff;
}
*{margin:0;padding:0;box-sizing:border-box}
html,body{width:926px;height:1200px;overflow:hidden;background:var(--white);font-family:'Roboto',sans-serif;color:var(--ink)}
.page{position:relative;width:926px;height:1200px}
.abs{position:absolute}
.header{left:0;top:0;width:926px;height:89px;background:var(--white)}
.brand{left:88px;top:30px;display:flex;align-items:center;gap:8px;font-family:'Exo 2',sans-serif;font-weight:600;font-size:20px;color:var(--black);letter-spacing:.5px}
.brand-dot{width:22px;height:22px;border-radius:50%;background:var(--orange)}
.phone{right:87px;top:60px;font-size:10px;font-weight:500;display:flex;align-items:center;gap:4px}
.phone .or{color:#999}
.nav{left:0;top:89px;width:926px;height:48px;background:var(--black)}
.nav a{position:absolute;top:0;height:48px;line-height:48px;color:var(--white);font-family:'Exo 2',sans-serif;font-size:10px;font-weight:500;text-decoration:none;letter-spacing:.3px}
.nav a.active{background:var(--orange);width:73px;text-align:center}
.social{right:88px;top:104px;display:flex;gap:4px}
.social span{width:18px;height:18px;border-radius:50%;border:2px solid #fff;background:#2b4e8c}
.social span:nth-child(2){background:#1c9ad6}
.social span:nth-child(3){background:#1e6aa8}
.social span:nth-child(4){background:#d33b2c}
.hero{left:0;top:137px;width:926px;height:509px;background:linear-gradient(180deg,#c9b8a0 0%,#b39c80 35%,#8a6b52 60%,#6e5a4c 100%);box-shadow:0 8px 10px -4px rgba(0,0,0,.45)}
.band{left:0;top:388px;width:926px;height:82px;background:rgba(235,235,235,.72)}
.tagline{left:0;top:408px;width:926px;text-align:center;font-family:'Exo 2',sans-serif;font-size:31px;font-weight:500;color:var(--black);letter-spacing:.5px}
.arrow{width:14px;height:14px;border-radius:50%;background:#333;color:#fff;font-size:8px;line-height:14px;text-align:center}
.card{top:490px;width:367px;height:139px;background:rgba(225,225,225,.82)}
.card .thumb{position:absolute;left:29px;top:26px;width:86px;height:86px;border-radius:50%;border:2px solid var(--orange);background:linear-gradient(135deg,#4a3a30,#8b6c4e 55%,#2b2420)}
.card h2{position:absolute;left:132px;top:40px;font-family:'Exo 2',sans-serif;font-size:16px;font-weight:500;letter-spacing:.5px}
.card p{position:absolute;left:133px;top:61px;width:215px;font-size:8px;line-height:18.5px;color:#444}
.welcome-title{left:0;top:680px;width:926px;text-align:center;font-family:'Exo 2',sans-serif;font-size:16.5px;font-weight:500}
.welcome-sub{left:0;top:706px;width:926px;text-align:center;font-family:'Exo 2',sans-serif;font-size:12.5px}
.welcome-body{left:90px;top:730px;width:746px;text-align:center;font-size:8.3px;line-height:20px;color:var(--grey-text)}
.gallery{left:0;top:807px;width:926px;height:210px;background:var(--panel)}
.gallery h2{position:absolute;left:0;top:30px;width:926px;text-align:center;font-family:'Exo 2',sans-serif;font-size:16px;font-weight:500}
.shot{position:absolute;top:69px;width:172px;height:110px;border:2px solid #fff;box-shadow:0 4px 4px -2px rgba(0,0,0,.5)}
.newsletter{left:0;top:1017px;width:926px;height:123px;background:#0e0e0e}
.newsletter h2{position:absolute;left:0;top:16px;width:926px;text-align:center;color:#fff;font-family:'Exo 2',sans-serif;font-size:16px;font-weight:500;letter-spacing:.5px}
.newsletter .sub{position:absolute;left:0;top:45px;width:926px;text-align:center;color:#aaa;font-size:8.5px}
.field{position:absolute;top:65px;height:36px;background:#222;color:#999;font-size:9.5px;line-height:36px;padding-left:16px}
.submit{position:absolute;left:614px;top:65px;width:138px;height:36px;background:var(--orange);color:#fff;font-family:'Exo 2',sans-serif;font-weight:600;font-size:12px;text-align:center;line-height:36px}
.footer{left:0;top:1140px;width:926px;height:60px;background:var(--black);font-size:8.3px;color:#888}
.footer .copy{position:absolute;left:86px;top:26px}
.footer .copy a{color:var(--orange);text-decoration:none}
.footer .links{position:absolute;right:86px;top:26px}
</style>
</head>
<body>
<div class="page">
  <header class="abs header">
    <div class="abs brand"><span class="brand-dot"></span>BRAMBLEOAK</div>
    <div class="abs phone">
      <svg width="6" height="9" viewBox="0 0 6 9"><rect x=".5" y=".5" width="5" height="8" rx="1" fill="none" stroke="#e0431a"/></svg>
      555-210-4837 <span class="or">OR</span> 555-388-9126
    </div>
  </header>

  <nav class="abs nav">
    <a class="active" style="left:86px">HOME</a>
    <a style="left:188px">GALLERY</a>
    <a style="left:280px">SERVICES</a>
    <a style="left:376px">WARRANTY</a>
    <a style="left:481px">CONTACT</a>
  </nav>
  <div class="abs social"><span></span><span></span><span></span><span></span></div>

  <section class="abs hero" role="img" aria-label="Photo of a bright custom kitchen with white cabinets and a pendant light"></section>
  <div class="abs band"></div>
  <h1 class="abs tagline">JOINERY WITH SPIRIT</h1>
  <div class="abs arrow" style="left:247px;top:422px">&#9664;</div>
  <div class="abs arrow" style="left:664px;top:422px">&#9654;</div>

  <div class="abs card" style="left:86px">
    <div class="thumb" role="img" aria-label="Residential kitchen with island seating"></div>
    <h2>RESIDENTIAL</h2>
    <p>Lorem ipsum dolor sit amet, consectetuer adipiscing elit, sed diam nonummy nibh euismod tincidunt ut laoreet dolore magna aliquam erat volutpat.</p>
  </div>
  <div class="abs card" style="left:473px">
    <div class="thumb" role="img" aria-label="Business interior with bar counter"></div>
    <h2>BUSINESS</h2>
    <p>Ut wisi enim ad minim veniam, quis nostrud exerci tation ullamcorper suscipit lobortis nisl ut aliquip ex ea commodo consequat.</p>
  </div>

  <h2 class="abs welcome-title">WELCOME TO BRAMBLEOAK CUSTOM CABINETS</h2>
  <p class="abs welcome-sub">Our passion is to deliver inspired cabinetry solutions to suit all your needs, supported by our phenomenal star class customer service</p>
  <p class="abs welcome-body">Lorem ipsum dolor sit amet, consectetuer adipiscing elit, sed diam nonummy nibh euismod tincidunt ut laoreet dolore magna aliquam erat volutpat. Ut wisi enim ad minim veniam, quis nostrud exerci tation ullamcorper suscipit lobortis nisl ut aliquip ex ea commodo consequat. Duis autem vel eum iriure dolor in hendrerit in vulputate velit esse molestie consequat, vel illum dolore eu feugiat nulla facilisis at vero eros et accumsan et iusto odio dignissim qui blandit praesent luptatum zzril delenit augue duis dolore te feugait nulla facilisi.</p>

  <section class="abs gallery">
    <h2>OUR GALLERY</h2>
    <div class="abs arrow" style="left:53px;top:118px">&#9664;</div>
    <div class="shot" style="left:86px;background:linear-gradient(135deg,#6b6058,#2a2422 60%,#8a7a6a)" role="img" aria-label="Bedroom with dark built-in cabinetry"></div>
    <div class="shot" style="left:278px;background:linear-gradient(135deg,#3a302a,#8b6844 55%,#5a3e28)" role="img" aria-label="Kitchen bar with stools"></div>
    <div class="shot" style="left:472px;background:linear-gradient(135deg,#d8d2c6,#6f6458 55%,#2e2a26)" role="img" aria-label="White kitchen with pendant lights"></div>
    <div class="shot" style="left:665px;background:linear-gradient(135deg,#e4e0d8,#a89a88 50%,#2a2624)" role="img" aria-label="Kitchen with cream cabinets and dark island"></div>
    <div class="abs arrow" style="left:855px;top:118px">&#9654;</div>
  </section>

  <section class="abs newsletter">
    <h2>NEWSLETTER SIGN UP</h2>
    <p class="sub">SUBSCRIBE TO OUR MAILING LIST</p>
    <div class="field" style="left:169px;width:206px">Name</div>
    <div class="field" style="left:387px;width:216px">Email Address</div>
    <div class="submit">SUBMIT</div>
  </section>

  <footer class="abs footer">
    <p class="copy">© 2015 Brambleoak Custom Cabinets. All Right Reserved. &nbsp;<a>Privacy Policy</a> &nbsp;|&nbsp; <a>Terms of Service</a></p>
    <p class="links">Home &nbsp;|&nbsp; Gallery &nbsp;|&nbsp; Services &nbsp;|&nbsp; Warranty &nbsp;|&nbsp; Contact</p>
  </footer>
</div>
</body>
</html>
```